Fun, Clean Business Card For Family Focused Travel Agency

I need a business card using specific colors and fonts as in the uploaded files. Ideally, I would like a large image of the logo on the back and all the contact info on the front. Maybe the stars/dots somewhere in a flowy form.

I do want it the contact information to be clear and easy to read. I don't want it to look too busy. Maybe even a bit minimalist.

I plan or ordering the ROUNDED CORNER business cards from Cardwell Press, so please consider that in your design.

Target Market(s)

Families with children, couples, groups of friends

Contact Information for Business Card

Marla Quint, Owner
Marla@TumbleTrips.example
Cell Phone Number 555-218-4603
Office Phone Number 555-647-1925
Specializing in Glimmerland destinations, Pelican Bay Fun Park, Cruises and All-Inclusive Vacations.

Nice but not required:
www.TumbleTrips.example
Facebook, Instagram, Twitter icons with username: TumbleTrips

Font styles to use
Sans Serif

Requirements
Must have
• Please try to use the colors from the logo as much as possible. I understand lighter shades/colors may be needed for some things.
Should not have
• NO SERIF FONTS. That is really the only thing I do not want at all

```html
<!DOCTYPE html>
<html lang="en">
<head>
<meta charset="utf-8">
<title>TumbleTrips Business Card</title>
<link href="https://fonts.googleapis.com/css2?family=Open+Sans:wght@400;600;700&display=swap" rel="stylesheet">
<style>
  :root {
    --page: #141618;
    --card: #1f2326;
    --ink: #f2f2f2;
    --silver: #a9adb0;
    --teal: #1fb394;
    --emblem-a: #2a3034;
    --emblem-b: #3b4347;
  }
  * { box-sizing: border-box; margin: 0; padding: 0; }
  html, body {
    width: 1200px; height: 800px; overflow: hidden;
    background: var(--page);
    font-family: "Open Sans", Arial, sans-serif;
    color: var(--ink);
  }
  .stage {
    width: 1200px; height: 800px;
    display: flex; align-items: center; justify-content: center; gap: 48px;
  }
  .card {
    width: 540px; height: 309px;
    background: var(--card);
    border-radius: 22px;
    position: relative;
    overflow: hidden;
  }

  /* Back */
  .card-back { display: flex; flex-direction: column; align-items: center; justify-content: center; }
  .brand-lockup { display: flex; align-items: center; gap: 22px; }
  .emblem {
    width: 96px; height: 104px; border-radius: 48px 48px 20px 20px;
    background: linear-gradient(160deg, var(--emblem-b), var(--emblem-a));
  }
  .brand-name { font-size: 46px; font-weight: 700; color: var(--silver); letter-spacing: 0.5px; }
  .specialty { margin-top: 34px; text-align: center; font-size: 14px; line-height: 1.55; color: var(--ink); }
  .specialty strong { font-weight: 700; }

  /* Front */
  .card-front { display: flex; padding: 42px 34px 34px 40px; }
  .contact { flex: 1; display: flex; flex-direction: column; }
  .person-name { font-size: 25px; font-weight: 600; line-height: 1.1; }
  .person-role { font-size: 15px; color: var(--teal); margin-top: 2px; }
  .divider { border-top: 2px dotted var(--teal); margin: 14px 0; width: 250px; }
  .contact-list { list-style: none; display: flex; flex-direction: column; gap: 7px; }
  .contact-list li { display: flex; align-items: center; gap: 10px; font-size: 14px; }
  .icon-dot {
    width: 20px; height: 20px; border-radius: 50%; background: var(--teal);
    display: flex; align-items: center; justify-content: center; flex: none;
  }
  .website { font-size: 15px; font-weight: 600; }
  .website .accent { color: var(--teal); }
  .social { display: flex; align-items: center; gap: 7px; margin-top: 16px; }
  .social-square { width: 26px; height: 26px; background: var(--teal); border-radius: 3px; }
  .social-handle { margin-left: 10px; font-size: 14px; font-weight: 600; }
  .front-brand { display: flex; flex-direction: column; align-items: center; justify-content: center; gap: 14px; width: 190px; }
  .front-brand .emblem {
    width: 86px; height: 94px;
    background: linear-gradient(160deg, var(--teal) 0%, #e28a3b 55%, #4a79c9 100%);
  }
  .front-brand .brand-name { font-size: 30px; color: var(--ink); }
</style>
</head>
<body>
<main class="stage">
  <section class="card card-back" aria-label="Card back">
    <div class="brand-lockup">
      <div class="emblem" role="img" aria-label="Brand emblem illustration with scattered stars"></div>
      <span class="brand-name">TumbleTrips</span>
    </div>
    <p class="specialty">
      <strong>Specializing in</strong> Glimmerland destinations<br>
      Pelican Bay Fun Park | Cruises and All-Inclusive Vacations.
    </p>
  </section>

  <section class="card card-front" aria-label="Card front">
    <div class="contact">
      <h1 class="person-name">Marla Quint</h1>
      <p class="person-role">Owner</p>
      <div class="divider"></div>
      <ul class="contact-list">
        <li>
          <span class="icon-dot"><svg width="10" height="12" viewBox="0 0 10 12"><rect x="1.5" y="0.5" width="7" height="11" rx="1.5" fill="none" stroke="#1f2326" stroke-width="1.4"/><circle cx="5" cy="9.3" r="0.8" fill="#1f2326"/></svg></span>
          555-218-4603
        </li>
        <li>
          <span class="icon-dot"><svg width="12" height="12" viewBox="0 0 12 12"><path d="M2.5 1.5 L4.5 1.5 L5.3 4 L4 5 Q5 7.2 7 8 L8 6.7 L10.5 7.5 L10.5 9.5 Q10.5 10.5 9.3 10.5 Q1.5 10 1.5 2.7 Q1.5 1.5 2.5 1.5 Z" fill="#1f2326"/></svg></span>
          555-647-1925
        </li>
        <li>
          <span class="icon-dot"><svg width="12" height="9" viewBox="0 0 12 9"><rect x="0.7" y="0.7" width="10.6" height="7.6" rx="1" fill="none" stroke="#1f2326" stroke-width="1.3"/><path d="M1 1 L6 5 L11 1" fill="none" stroke="#1f2326" stroke-width="1.3"/></svg></span>
          Marla@TumbleTrips.example
        </li>
      </ul>
      <div class="divider"></div>
      <p class="website">www.<span class="accent">TumbleTrips</span>.example</p>
      <div class="social">
        <span class="social-square" aria-hidden="true"></span>
        <span class="social-square" aria-hidden="true"></span>
        <span class="social-square" aria-hidden="true"></span>
        <span class="social-handle">TumbleTrips</span>
      </div>
    </div>
    <div class="front-brand">
      <div class="emblem" role="img" aria-label="Colourful brand emblem illustration with scattered stars"></div>
      <span class="brand-name">TumbleTrips</span>
    </div>
  </section>
</main>
</body>
</html>
```